Leaflet to promote a new sports massage business

I am a Remedial and Sports Massage therapist and treat a range of people from professionals who spend hours working behind computers and have associated neck and back pain through poor posture to amateur sports people of varying intensity/ability - who encounter injuries along the way, or just need some good old stretching out.Remedial and sports massage helps people who have musculoskeletal injury, pain or dysfunction brought about by the stresses and strains of life. Through massage i can reduce pain, promote recovery after injury, relieve stress, and improve flexibility. All of this contributes to helping people feel better. I have just started working at a new location (address attached) and am looking to raise awareness that I am there and to promote the benefits of massage to encourage new clients(attached as a separate document). I have a business card (attached to the brief) which uses hands as the main device, I would like to include these – possibly in some sort of logo and I would like to use purple as a key colour (if colour is used). I also want to include the KTVB logo (attached) to add credibility

```html
<!DOCTYPE html>
<html lang="en">
<head>
<meta charset="utf-8">
<title>Hannah Lorrimer – Remedial and Sports Massage Leaflet</title>
<link rel="stylesheet" href="https://fonts.googleapis.com/css2?family=Roboto+Condensed:wght@400;700&family=Open+Sans:wght@400;600&family=Cabin:wght@400&display=swap">
<style>
  :root {
    --backdrop: #a87c55;
    --paper: #ffffff;
    --brand-blue: #1f80bf;
    --band-blue: #2195c4;
    --purple: #5b0a55;
    --purple-deep: #4a0647;
    --gold-light: #f6c21c;
    --gold-dark: #d98a12;
    --ink-grey: #555555;
    --ink-dark: #1c1c1c;
    --white: #ffffff;
  }
  * { margin: 0; padding: 0; box-sizing: border-box; }
  html, body { width: 941px; height: 1200px; overflow: hidden; }
  body { background: var(--backdrop); position: relative; font-family: "Open Sans", Arial, sans-serif; }

  .leaflet {
    position: absolute; left: 108px; top: 95px; width: 710px; height: 1002px;
    background: var(--paper); box-shadow: 4px 5px 8px rgba(0,0,0,.35); overflow: hidden;
  }
  .title {
    position: absolute; left: 42px; top: 27px; width: 620px;
    font-family: "Roboto Condensed", Arial, sans-serif; font-weight: 700;
    font-size: 40px; line-height: 48px; color: var(--brand-blue);
  }
  .subtitle {
    position: absolute; left: 42px; top: 130px;
    font-family: "Cabin", Arial, sans-serif; font-size: 33px; color: var(--ink-grey);
  }
  .band-left { position: absolute; left: 0; top: 205px; width: 102px; height: 35px; background: var(--band-blue); }
  .band-right { position: absolute; left: 180px; top: 205px; width: 530px; height: 35px; background: var(--band-blue); }
  .social {
    position: absolute; right: 24px; top: 210px;
    font-family: "Open Sans", Arial, sans-serif; font-size: 19px; color: var(--white);
    display: flex; align-items: center; gap: 8px;
  }
  .social .dot { width: 20px; height: 20px; border-radius: 50%; background: var(--white); }

  .hero-photo {
    position: absolute; left: 80px; top: 240px; width: 630px; height: 292px;
    background: linear-gradient(100deg, #ffffff 0%, #f3ddc7 30%, #e9c4a2 60%, #d6a77f 85%, #c99e78 100%);
  }
  .hands-mark {
    position: absolute; left: 0; top: 315px; width: 200px; height: 200px;
  }
  .logo {
    position: absolute; left: 48px; top: 198px; width: 130px; height: 92px;
    display: flex; align-items: center; gap: 8px;
  }
  .logo .mark { width: 30px; height: 30px; border-radius: 50%; background: var(--band-blue); }
  .logo .name {
    font-family: "Open Sans", Arial, sans-serif; font-weight: 600; font-size: 20px;
    letter-spacing: 3px; color: #2b2a6e;
  }

  .purple-panel { position: absolute; left: 0; top: 531px; width: 710px; height: 471px; background: var(--purple); }

  .email-tab {
    position: absolute; left: 62px; top: 503px; width: 424px; height: 42px;
    background: linear-gradient(90deg, var(--gold-dark), var(--gold-light) 50%, var(--gold-dark));
    border-radius: 24px 24px 0 0;
    font-family: "Roboto Condensed", Arial, sans-serif; font-weight: 700;
    font-size: 25px; color: var(--white); text-align: center; line-height: 42px; letter-spacing: .5px;
  }

  .intro {
    position: absolute; left: 29px; top: 570px; width: 353px;
    color: var(--white); font-size: 12.6px; line-height: 17.8px; text-align: justify;
  }
  .intro p + p { margin-top: 9px; }

  .benefits-heading {
    position: absolute; left: 0; top: 815px; width: 380px; height: 28px;
    background: linear-gradient(90deg, var(--gold-light), var(--gold-dark));
    padding-left: 29px; font-weight: 600; font-size: 18px; line-height: 28px; color: var(--ink-dark);
  }
  .benefits {
    position: absolute; left: 29px; top: 854px; list-style: none;
    color: var(--white); font-size: 16px; line-height: 23px;
  }
  .benefits li { display: flex; align-items: center; gap: 12px; }
  .benefits svg { width: 15px; height: 15px; flex: none; }

  .contact-box {
    position: absolute; left: 413px; top: 573px; width: 264px; height: 387px;
    background: linear-gradient(135deg, var(--gold-light), var(--gold-dark));
  }
  .photo { position: absolute; left: 12px; width: 242px; border: 1px solid var(--white); }
  .photo-leg { top: 12px; height: 115px; background: linear-gradient(120deg, #e8d7c9, #c99c7d 55%, #e7e0da); }
  .photo-back { top: 134px; height: 141px; background: linear-gradient(120deg, #f2efea, #d8b39a 50%, #b99a86); }
  .address { position: absolute; top: 282px; width: 100%; text-align: center; font-size: 12.5px; line-height: 17px; color: var(--ink-dark); }
  .contact-label { position: absolute; top: 322px; width: 100%; text-align: center; font-size: 19px; color: var(--ink-dark); }
  .phone {
    position: absolute; top: 345px; width: 100%; text-align: center;
    font-family: "Roboto Condensed", Arial, sans-serif; font-weight: 700; font-size: 33px; color: var(--ink-dark);
  }
</style>
</head>
<body>
  <main class="leaflet">
    <h1 class="title">Hannah Lorrimer: Remedial and Sports Massage Therapist</h1>
    <p class="subtitle">Stride Physiotherapy</p>

    <div class="hero-photo" role="img" aria-label="Photo of a therapist's hands massaging a smiling woman's shoulder"></div>
    <svg class="hands-mark" role="img" aria-label="Purple illustration of open hands" viewBox="0 0 200 200">
      <path d="M0 60 L60 20 L120 70 L180 200 L0 200 Z" fill="var(--purple)"/>
    </svg>

    <div class="band-left"></div>
    <div class="band-right"></div>
    <div class="social"><span class="dot"></span>social: /HannahLorrimerMassage</div>

    <div class="logo"><span class="mark"></span><span class="name">KTVB</span></div>

    <section class="purple-panel"></section>
    <div class="email-tab">hannahlorrimer@mailbox.com</div>

    <div class="intro">
      <p>I am a Remedial and Sports Massage therapist and treat a range of people from professionals who spend hours working behind computers and have associated neck and back pain through poor posture to amateur sports people of varying intensity/ability - who encounter injuries along the way, or just need some good old stretching out.</p>
      <p>Remedial and sports massage helps people who have musculoskeletal injury, pain or dysfunction brought about by the stresses and strains of life. Through massage i can reduce pain, promote recovery after injury, relieve stress, and improve flexibility. All of this contributes to helping people feel better.</p>
    </div>

    <h2 class="benefits-heading">BENEFITS OF MASSAGE</h2>
    <ul class="benefits">
      <li><svg viewBox="0 0 15 15"><rect x="1" y="2" width="12" height="12" fill="none" stroke="#f6c21c" stroke-width="1.6"/><path d="M3.5 8 L6.5 11 L14 1.5" fill="none" stroke="#f6c21c" stroke-width="2"/></svg>Reduces pain</li>
      <li><svg viewBox="0 0 15 15"><rect x="1" y="2" width="12" height="12" fill="none" stroke="#f6c21c" stroke-width="1.6"/><path d="M3.5 8 L6.5 11 L14 1.5" fill="none" stroke="#f6c21c" stroke-width="2"/></svg>Promotes recovery</li>
      <li><svg viewBox="0 0 15 15"><rect x="1" y="2" width="12" height="12" fill="none" stroke="#f6c21c" stroke-width="1.6"/><path d="M3.5 8 L6.5 11 L14 1.5" fill="none" stroke="#f6c21c" stroke-width="2"/></svg>Improves posture and flexibility</li>
      <li><svg viewBox="0 0 15 15"><rect x="1" y="2" width="12" height="12" fill="none" stroke="#f6c21c" stroke-width="1.6"/><path d="M3.5 8 L6.5 11 L14 1.5" fill="none" stroke="#f6c21c" stroke-width="2"/></svg>Relieves stress</li>
      <li><svg viewBox="0 0 15 15"><rect x="1" y="2" width="12" height="12" fill="none" stroke="#f6c21c" stroke-width="1.6"/><path d="M3.5 8 L6.5 11 L14 1.5" fill="none" stroke="#f6c21c" stroke-width="2"/></svg>Improves health and wellbeing</li>
    </ul>

    <aside class="contact-box">
      <div class="photo photo-leg" role="img" aria-label="Photo of hands massaging a calf muscle"></div>
      <div class="photo photo-back" role="img" aria-label="Photo of a therapist treating a client lying on a massage table"></div>
      <p class="address">Ashcombe Athletic Ground,<br>Millbrook Road, Ashcombe, AB1 2CD</p>
      <p class="contact-label">Contact Us Now</p>
      <p class="phone">07700 900123</p>
    </aside>
  </main>
</body>
</html>
```